Harborview Estates Business Card for Apartment Buildings

Create business cards for resident managers who run apartment buildings. The audience is the public who are searching for apartment rentals, and current residents who live at the apartment building. Key design element will be incorporating the company logo, however, the logo cannot dominate. The building name and manager name are more important than the logo. Current business card design leaves little room for copy, so we may need to reduce the size on the current card to allow for more space for copy.

Target Market(s)

Adults 18-65 years of age, who are looking for an apartment rental, plus current residents who live at our apartment buildings.

Industry/Entity Type

Property Management

Contact Information for Business Card

A major design element will be use of the company logo. Important property and manager contact information must be part of the design. The size of the logo will need to be reduced to make room for building and manager contact copy.

Font styles to use
Sans Serif

Colors
3176b5
000000
959595
ffffff

Requirements
Must have
• 1) Incorporate the company logo.
• 2) Use the company colors (dark blue, black/grey, over white).
• 3) FEATURE THE BUILDING NAME
• 4) FEATURE THE MANAGER NAME
• 5) The company name is less important than BUILDING and MANAGER
• 6) Manager contact information
• **SEE ATTACHED CREATIVE BRIEF**
Nice to have
• 1) Back of card logo watermark
• 2) Ability to write notes on back of carfd
Should not have
• Avoid letting the company logo dominate the card, the building name and manager are more important than the company logo.

```html
<!DOCTYPE html>
<html lang="en">
<head>
<meta charset="utf-8">
<title>Harborview Estates – Business Card</title>
<link href="https://fonts.googleapis.com/css2?family=Fjalla+One&family=Lato:wght@400;700&display=swap" rel="stylesheet">
<style>
  :root {
    --brand-blue: #176fae;
    --ink: #2b2b2b;
    --grey-line: #4a4a4a;
    --paper: #ffffff;
    --backdrop: #1a1a1a;
  }
  * { margin: 0; padding: 0; box-sizing: border-box; }
  html, body { width: 1200px; height: 897px; overflow: hidden; background: var(--backdrop); }
  .canvas { position: relative; width: 1200px; height: 897px; }

  .card {
    position: absolute; left: 303px; width: 595px; height: 339px;
    border-radius: 20px; overflow: hidden;
    font-family: "Lato", Arial, sans-serif;
  }
  .card--front { top: 92px; background: var(--paper); }
  .card--back { top: 469px; background: var(--brand-blue); }

  .card__shapes { position: absolute; inset: 0; }

  .manager { position: absolute; left: 29px; top: 44px; color: var(--paper); }
  .manager__name { font-family: "Fjalla One", "Arial Narrow", sans-serif; font-size: 29px; line-height: 1; letter-spacing: -0.2px; }
  .manager__title { font-size: 14px; margin-top: 3px; }

  .brand {
    position: absolute; display: flex; align-items: center; gap: 8px;
    font-family: "Lato", Arial, sans-serif; font-weight: 700;
  }
  .brand__dot { border-radius: 50%; flex: none; }
  .brand--front { right: 30px; top: 54px; color: var(--brand-blue); font-size: 23px; }
  .brand--front .brand__dot { width: 16px; height: 16px; background: var(--brand-blue); }
  .brand--back { left: 0; right: 0; top: 150px; justify-content: center; color: var(--paper); font-size: 42px; gap: 14px; }
  .brand--back .brand__dot { width: 30px; height: 30px; background: var(--paper); }

  .contacts { position: absolute; left: 29px; top: 200px; list-style: none; color: var(--ink); font-size: 14.5px; }
  .contacts li { display: flex; align-items: center; height: 19.4px; }
  .contacts svg { width: 10px; height: 10px; margin-right: 12px; fill: var(--brand-blue); flex: none; }

  .property { position: absolute; right: 30px; top: 227px; text-align: right; color: var(--ink); font-size: 14.5px; line-height: 19.4px; }
  .property__name { color: var(--brand-blue); font-size: 18px; line-height: 22px; }

  .website { position: absolute; left: 0; right: 0; top: 291px; text-align: center; color: var(--paper); font-size: 15.5px; letter-spacing: 0.6px; }
</style>
</head>
<body>
<main class="canvas">

  <section class="card card--front" aria-label="Card front">
    <svg class="card__shapes" viewBox="0 0 595 339" aria-hidden="true">
      <path d="M0 30 H346 C322 46 316 88 340 105 H0 Z" fill="var(--brand-blue)"/>
      <path d="M0 322 H345 L338 328 H0 Z" fill="var(--grey-line)"/>
      <path d="M0 332 H350 C385 332 395 316 432 316 H595 V339 H0 Z" fill="var(--brand-blue)"/>
    </svg>

    <div class="manager">
      <h1 class="manager__name">MARISOL DELGADO</h1>
      <p class="manager__title">Resident Manager</p>
    </div>

    <div class="brand brand--front"><span class="brand__dot"></span>Harborview Estates</div>

    <ul class="contacts">
      <li><svg viewBox="0 0 10 10"><path d="M2 0 L4 2.5 L3 3.8 C3.6 5 4.8 6.3 6.2 7 L7.5 6 L10 8 L8.5 10 C4 9.5 0.5 6 0 1.5 Z"/></svg>555-210-4836</li>
      <li><svg viewBox="0 0 10 10"><rect x="2.5" y="0" width="5" height="3"/><rect x="0" y="3.5" width="10" height="4" rx="1"/><rect x="2.5" y="7" width="5" height="3"/></svg>555-210-4837</li>
      <li><svg viewBox="0 0 10 10"><path d="M2.5 0 H7.5 V10 H2.5 Z M3.5 1 V8 H6.5 V1 Z"/></svg>555-382-9154</li>
      <li><svg viewBox="0 0 10 10"><path d="M0 1.5 H10 V8.5 H0 Z M1 2.5 L5 5.5 L9 2.5 V7.5 H1 Z" fill-rule="evenodd"/></svg>marisol@harborviewestates.com</li>
      <li><svg viewBox="0 0 10 10"><circle cx="5" cy="5" r="4.5" fill="none" stroke="var(--brand-blue)"/><path d="M0.5 5 H9.5 M5 0.5 C2.5 3 2.5 7 5 9.5 M5 0.5 C7.5 3 7.5 7 5 9.5" fill="none" stroke="var(--brand-blue)" stroke-width="0.8"/></svg>www.harborviewestates.com</li>
    </ul>

    <address class="property" style="font-style: normal;">
      <div class="property__name">Cedar Court Apartments</div>
      <div>1482 Linden Avenue</div>
      <div>Fairhaven, CA 92010</div>
    </address>
  </section>

  <section class="card card--back" aria-label="Card back">
    <div class="brand brand--back"><span class="brand__dot"></span>Harborview Estates</div>
    <p class="website">www.harborviewestates.com</p>
  </section>

</main>
</body>
</html>
```